Judicial election website to attract voters

I need a simple one-page web design for a judicial election. I'm going to put up one picture, maybe two. The picture I have needs a little touch-up (whiten teeth for example). I have 3 paragraphs of text. I'd like a "Donate" button that can link to a CoinDrift account. I'd also like a little background design, like the Constitution or something like that. There's a couple other little things but that's the bulk of it.

Target Market(s)

Involved voters and some media

Industry/Entity Type

Legal

Number of Pages Required

1 page

Font styles to use
Sans Serif

Requirements
Must have
• My picture, text, donate button
• Phrase "Remember to vote August 30, 2016!"
Nice to have
• Perhaps a second photo, maybe a short 30 second video of me talking directly to the voters, cool background: Constitution, something judgey.
Should not have
• Not sure ... profanity, I guess.

```html
<!DOCTYPE html>
<html lang="en">
<head>
<meta charset="utf-8">
<title>Civic Ballot</title>
<link href="https://fonts.googleapis.com/css2?family=Jost:wght@300;400&family=Didact+Gothic&display=swap" rel="stylesheet">
<style>
  :root {
    --navy: #12266b;
    --red: #c8102e;
    --ink: #333333;
    --soft: #f4f4f4;
    --bar: #3a3a3a;
    --white: #ffffff;
  }
  * { margin: 0; padding: 0; box-sizing: border-box; }
  html, body { width: 809px; height: 1200px; overflow: hidden; background: var(--white); }
  body { position: relative; font-family: "Didact Gothic", sans-serif; color: var(--ink); }
  .heading { font-family: "Jost", sans-serif; font-weight: 400; color: var(--navy); text-transform: uppercase; letter-spacing: 0.2px; }
  .heading .accent { color: var(--red); }

  .site-header { position: absolute; top: 0; left: 0; width: 809px; height: 76px; }
  .brand { position: absolute; font-family: "Didact Gothic", sans-serif; font-weight: 400; color: var(--navy); font-size: 21px; line-height: 1; }
  .site-header .brand { left: 66px; top: 27px; }
  .donate-button {
    position: absolute; width: 100px; height: 31px;
    background: var(--navy); border-bottom: 2px solid var(--red);
    color: var(--white); font-family: "Jost", sans-serif; font-weight: 400; font-size: 13px; letter-spacing: 0.5px;
    display: flex; align-items: center; justify-content: center; gap: 7px; text-decoration: none;
  }
  .site-header .donate-button { left: 642px; top: 23px; }

  .hero { position: absolute; top: 76px; left: 0; width: 809px; height: 323px;
    background: linear-gradient(180deg, #5c6a2c 0%, #3f5222 45%, #55602e 70%, #7a3a3a 100%); }
  .hero-panel { position: absolute; left: 183px; top: 26px; width: 429px; height: 297px;
    background: linear-gradient(160deg, #2b4391 0%, #2a4088 55%, #3a4f8c 100%); }
  .hero-title { position: absolute; left: 183px; top: 110px; width: 429px; text-align: center;
    font-family: "Jost", sans-serif; font-weight: 300; font-size: 37px; line-height: 57px; color: var(--white); letter-spacing: 0.5px; }
  .hero-title .date { display: block; color: var(--red); }
  .hero-arrow { position: absolute; top: 140px; }
  .hero-arrow.prev { left: 24px; }
  .hero-arrow.next { left: 766px; }

  .video-section { position: absolute; top: 399px; left: 0; width: 809px; height: 359px; text-align: center; }
  .video-section .heading { position: absolute; top: 28px; width: 100%; font-size: 19px; }
  .intro { position: absolute; top: 62px; left: 170px; width: 469px; font-size: 12px; line-height: 17.5px; }
  .video-frame { position: absolute; left: 231px; top: 115px; width: 347px; height: 209px;
    border: 1px solid #cfcfcf; border-radius: 3px; background: var(--white); padding: 3px; }
  .video-poster { width: 339px; height: 173px; border-radius: 2px 2px 0 0;
    background: linear-gradient(120deg, #b8553f 0%, #6a7fa8 40%, #e9e4dc 50%, #8b5d86 75%, #c24a4a 100%); position: relative; }
  .play-badge { position: absolute; left: 152px; top: 77px; width: 30px; height: 30px; }
  .video-controls { height: 29px; background: #1d1d1d; border-radius: 0 0 3px 3px; display: flex; align-items: center;
    font-size: 10px; color: var(--white); }
  .ctrl-play { width: 29px; height: 29px; background: #2c2c2c; display: flex; align-items: center; justify-content: center; }
  .time { margin: 0 7px; }
  .track { width: 187px; height: 9px; border-radius: 5px; background: #3a3a3a; position: relative; }
  .track .played { position: absolute; left: 0; top: 0; width: 67px; height: 9px; border-radius: 5px; background: var(--red); }
  .track .knob { position: absolute; left: 62px; top: -1px; width: 11px; height: 11px; border-radius: 50%; background: #e6e6e6; }

  .about { position: absolute; top: 758px; left: 0; width: 809px; height: 347px; background: var(--soft); }
  .portrait { position: absolute; left: 68px; top: 32px; width: 218px; height: 283px;
    background: linear-gradient(180deg, #c9ccd2 0%, #c7b39a 45%, #d9a27e 70%, #e08a63 100%); }
  .about-copy { position: absolute; left: 321px; top: 30px; width: 420px; }
  .about-copy .heading { font-size: 19px; margin-bottom: 14px; }
  .about-copy p { font-size: 12px; line-height: 17.5px; margin-bottom: 10px; }

  .site-footer { position: absolute; top: 1105px; left: 0; width: 809px; height: 66px; }
  .social { position: absolute; left: 67px; top: 24px; display: flex; gap: 6px; }
  .social a { font-size: 10px; color: var(--navy); text-decoration: none; display: flex; align-items: center; gap: 3px; }
  .social a span { width: 8px; height: 8px; background: var(--navy); display: inline-block; }
  .site-footer .brand { left: 0; width: 809px; text-align: center; top: 25px; font-size: 18px; }
  .site-footer .donate-button { left: 642px; top: 19px; }
  .copyright { position: absolute; top: 1171px; left: 0; width: 809px; height: 29px; background: var(--bar);
    color: var(--white); font-family: "Jost", sans-serif; font-size: 9px; text-align: center; line-height: 29px; text-transform: uppercase; }
</style>
</head>
<body>
  <header class="site-header">
    <div class="brand">Civic Ballot</div>
    <a class="donate-button" href="#" aria-label="Donate via CoinDrift">
      <svg width="16" height="14" viewBox="0 0 16 14" aria-hidden="true"><circle cx="10" cy="5" r="4" fill="none" stroke="#fff" stroke-width="1.4"/><path d="M1 12 L5 9 L9 10 L13 9" fill="none" stroke="#fff" stroke-width="1.4"/></svg>
      DONATE
    </a>
  </header>

  <section class="hero">
    <div class="hero-panel" role="img" aria-label="Voter placing a ballot in a box in front of a flag"></div>
    <h1 class="hero-title">REMEMBER TO VOTE<span class="date">AUGUST 30, 2016!</span></h1>
    <svg class="hero-arrow prev" width="20" height="40" viewBox="0 0 20 40" aria-hidden="true"><path d="M19 1 L1 20 L19 39" fill="none" stroke="#fff" stroke-width="1.2"/></svg>
    <svg class="hero-arrow next" width="20" height="40" viewBox="0 0 20 40" aria-hidden="true"><path d="M1 1 L19 20 L1 39" fill="none" stroke="#fff" stroke-width="1.2"/></svg>
  </section>

  <section class="video-section">
    <h2 class="heading">Watch my <span class="accent">Video</span></h2>
    <p class="intro">Lorem ipsum dolor sit amet consectetuer adipiscing elit, sed diam nonummy nibh euismod tincidunt ut laoreet dolore magna aliquam erat volutpat.</p>
    <div class="video-frame">
      <div class="video-poster" role="img" aria-label="Hands holding an Elections 2016 sign">
        <svg class="play-badge" viewBox="0 0 30 30" aria-hidden="true"><circle cx="15" cy="15" r="15" fill="#fff"/><path d="M12 9 L21 15 L12 21 Z" fill="#111"/></svg>
      </div>
      <div class="video-controls">
        <div class="ctrl-play"><svg width="9" height="10" viewBox="0 0 9 10" aria-hidden="true"><path d="M0 0 L9 5 L0 10 Z" fill="#fff"/></svg></div>
        <span class="time">04:59</span>
        <div class="track"><div class="played"></div><div class="knob"></div></div>
        <span class="time">10:35</span>
        <svg width="14" height="12" viewBox="0 0 14 12" aria-hidden="true"><path d="M0 4 H3 L7 0 V12 L3 8 H0 Z" fill="#fff"/><path d="M9 3 Q11 6 9 9 M11 1 Q14 6 11 11" fill="none" stroke="#fff" stroke-width="1"/></svg>
        <svg style="margin-left:10px" width="14" height="14" viewBox="0 0 14 14" aria-hidden="true"><path d="M1 1 L6 6 M1 1 H5 M1 1 V5 M13 13 L8 8 M13 13 H9 M13 13 V9" stroke="#fff" stroke-width="1.6" fill="none"/></svg>
      </div>
    </div>
  </section>

  <section class="about">
    <div class="portrait" role="img" aria-label="Portrait photo of the candidate"></div>
    <div class="about-copy">
      <h2 class="heading">About <span class="accent">Me</span></h2>
      <p>Lorem ipsum dolor sit amet, consectetuer adipiscing elit, sed diam nonum nibh euismod tincidunt ut laoreet dolore magna aliquam erat volutpat. Ut wisi enim ad minim veniam, quis nostrud exerci tation ullamcorper suscipit lobortis nisl ut aliquip ex ea commodo consequat.</p>
      <p>Lorem ipsum dolor sit amet, consectetuer adipiscing elit, sed diam nonum nibh euismod tincidunt ut laoreet dolore magna aliquam erat volutpat. Ut wisi enim ad minim veniam, quis nostrud exerci tation ullamcorper suscipit lobortis nisl ut aliquip ex ea commodo consequat.</p>
      <p>Lorem ipsum dolor sit amet, consectetuer adipiscing elit, sed diam nonum nibh euismod tincidunt ut laoreet dolore magna aliquam erat volutpat. Ut wisi enim ad minim veniam, quis nostrud exerci tation ullamcorper suscipit lobortis nisl ut aliquip ex ea commodo consequat Lorem ipsum dolor sit amet, consectetuer adipiscing elit, sed diam nonum.</p>
    </div>
  </section>

  <footer class="site-footer">
    <nav class="social" aria-label="Social links">
      <a href="#"><span></span>Friendly</a>
      <a href="#"><span></span>Chirper</a>
      <a href="#"><span></span>WorkNet</a>
      <a href="#"><span></span>Circles</a>
    </nav>
    <div class="brand">Civic Ballot</div>
    <a class="donate-button" href="#" aria-label="Donate via CoinDrift">
      <svg width="16" height="14" viewBox="0 0 16 14" aria-hidden="true"><circle cx="10" cy="5" r="4" fill="none" stroke="#fff" stroke-width="1.4"/><path d="M1 12 L5 9 L9 10 L13 9" fill="none" stroke="#fff" stroke-width="1.4"/></svg>
      DONATE
    </a>
  </footer>
  <div class="copyright">Copyright © 2016 Civic Ballot. All rights reserved.</div>
</body>
</html>
```